Business card design needed

Family General Practitioner/ Family Physician.
Logo is the logo of the Noble Guild of Family Healers Oceania
http://kpltw.varendo.example/ImageShelf/marks/pages/NGFHO%20mark_jpg.htm
Updates

Project Deadline Extended
Reason: Just a bit more time to make changes and the weekend for me to look at things closely and to choose. Thanks, Orin

Thanks for all the submissions. So many of them are really works of art. Not one of them are not good. The ones that I am eliminating are the ones that I think are not suitable for me personally only, and because if I don't, it makes it very difficult to decide as many of you are also sending me slight variations of a card. I have just decided to choose a second place card too. Can't thank you all enough. Good luck, Orin. P.S - Working today till 10 pm as the card says :-), so probably won't be able to give a feedback till late Saturday night or Sunday morning here in Sydney, Australia. 

Project Deadline Extended
Reason: Just added a second place to the budget and realised that Australia is ahead of the rest of the world in the time zone (only :-) - don't want to offend anyone or start a debate!! ) , so Monday deadline will mean it will be a weekend for the rest of the world. Just wanted to give everyone more time to submit their best, especially since I will be picking a second card too. Can't thank everyone enough for the submissions. P.S - Not keen on photos on the card.

Industry/Entity Type

Business

Contact Information for Business Card

Dr. Orin Halvey M.B.B.S., F.N.G.F.H.O
Family General Practitioner
Address, timings, phone and fax number on the back.

Requirements
Must have
• Timings
Mon 7 am - 7 pm
Tues 7 am - 12 pm
Wed 7 am - 10 pm
Thurs 7 am - 12 pm
Fri 7 am - 8 pm
Sat 8 am - 10 pm
Sun - Off

```html
<!DOCTYPE html>
<html lang="en">
<head>
<meta charset="utf-8">
<title>Dr Orin Halvey – Business Card</title>
<link rel="stylesheet" href="https://fonts.googleapis.com/css2?family=Cinzel:wght@400;500&family=Mulish:ital,wght@0,400;0,700;0,800;1,700&display=swap">
<style>
  :root {
    --stage: #ecebe8;
    --navy: #2b3192;
    --sky: #4fb3e0;
    --charcoal: #3a3a3c;
    --ink: #333438;
    --rule: #8b8f96;
    --paper: #ffffff;
    --ice-light: #e3eef9;
    --ice-deep: #b7d2ee;
  }
  * { margin: 0; padding: 0; box-sizing: border-box; }
  html, body { width: 1200px; height: 788px; overflow: hidden; }
  body {
    position: relative;
    background: var(--stage);
    font-family: "Mulish", "Century Gothic", sans-serif;
    color: var(--ink);
  }
  .card {
    position: absolute;
    width: 524px;
    height: 299px;
    border-radius: 18px;
    overflow: hidden;
    background: var(--paper);
  }

  /* Front */
  .card--front { left: 338px; top: 74px; }
  .card__wave { position: absolute; inset: 0; }
  .doctor-name {
    position: absolute; left: 32px; top: 24px;
    font-size: 27px; font-weight: 800; color: var(--navy); letter-spacing: 0.2px;
  }
  .doctor-quals {
    position: absolute; left: 33px; top: 58px;
    font-family: "Cinzel", serif; font-size: 18px; color: var(--navy); letter-spacing: 1.5px;
  }
  .doctor-role {
    position: absolute; left: 34px; top: 92px;
    font-family: "Cinzel", serif; font-size: 12.5px; color: var(--navy); letter-spacing: 0.6px;
  }
  .guild-mark {
    position: absolute; left: 32px; top: 138px; width: 120px;
    display: flex; align-items: flex-start; gap: 6px;
  }
  .guild-mark__dot {
    flex: none; width: 14px; height: 14px; border-radius: 50%; background: var(--navy); margin-top: 2px;
  }
  .guild-mark__name {
    font-size: 10.5px; line-height: 1.3; font-weight: 700; color: var(--navy);
  }
  .contact {
    position: absolute; right: 22px; top: 180px;
    text-align: right; color: var(--paper); font-size: 13px; line-height: 17px;
  }
  .contact__line b { font-style: italic; font-weight: 800; }
  .contact__phone { margin-bottom: 6px; }
  .contact__address { margin-top: 10px; }

  /* Backs */
  .card--back-photo { left: 54px; top: 446px; }
  .card--back-tint { left: 622px; top: 446px;
    background: linear-gradient(100deg, var(--ice-light) 0%, #cfe1f4 55%, var(--ice-deep) 100%); }
  .photo-area {
    position: absolute; inset: 0;
    background: linear-gradient(120deg, #dfe7d6 0%, #c9d8b8 35%, #d8dfe4 60%, #bfd0a9 100%);
  }
  .photo-veil { position: absolute; inset: 0; background: rgba(255,255,255,0.55); }
  .back__title {
    position: absolute; left: 0; right: 0; top: 14px; text-align: center;
    font-family: "Cinzel", serif; font-size: 21px; letter-spacing: 1px; color: var(--ink);
  }
  .back__rule-h { position: absolute; left: 0; right: 0; height: 1px; background: var(--rule); }
  .back__rule-h--top { top: 52px; }
  .back__rule-h--bottom { top: 262px; }
  .back__rule-v { position: absolute; left: 262px; top: 52px; width: 1px; height: 210px; background: var(--rule); }
  .timings { position: absolute; left: 44px; top: 62px; }
  .timings__heading {
    font-size: 16px; font-weight: 700; font-style: italic; margin-left: 28px; margin-bottom: 2px;
  }
  .timings__row { display: flex; font-size: 16px; line-height: 23.2px; }
  .timings__day { width: 60px; font-weight: 700; }
  .timings__hours { white-space: pre; }
  .appointment { position: absolute; left: 276px; top: 65px; width: 234px; font-size: 16px; }
  .appointment__heading { font-size: 18px; margin-bottom: 14px; }
  .field { display: flex; align-items: flex-end; height: 20px; margin-bottom: 20px; }
  .field__line { flex: 1; border-bottom: 1px solid var(--ink); margin-left: 4px; height: 16px; }
  .field__line--short { flex: 0 0 128px; margin-right: 6px; margin-left: 0; }
  .field--blank .field__line { margin-left: 8px; }
  .back__note {
    position: absolute; left: 0; right: 0; top: 275px; text-align: center;
    font-size: 10.5px; font-weight: 800; color: var(--ink);
  }
</style>
</head>
<body>

<section class="card card--front">
  <svg class="card__wave" viewBox="0 0 524 299" width="524" height="299" aria-hidden="true">
    <path d="M0,262 C130,300 270,258 370,182 C425,140 470,112 524,104 L524,299 L0,299 Z" fill="var(--navy)"/>
    <path d="M0,230 C140,282 280,248 375,176 C430,134 475,108 524,98" fill="none" stroke="var(--sky)" stroke-width="6"/>
    <path d="M0,240 C90,262 180,270 260,258" fill="none" stroke="var(--charcoal)" stroke-width="9" stroke-linecap="round"/>
  </svg>
  <h1 class="doctor-name">Dr Orin Halvey</h1>
  <p class="doctor-quals">M.B.B.S., F.N.G.F.H.O</p>
  <p class="doctor-role">Family General Practitioner</p>
  <div class="guild-mark">
    <span class="guild-mark__dot"></span>
    <span class="guild-mark__name">Noble Guild of Family Healers Oceania</span>
  </div>
  <div class="contact">
    <p class="contact__line contact__phone"><b>p :</b> 02 5550 1400</p>
    <p class="contact__line"><b>f :</b> 02 5550 1733</p>
    <p class="contact__address">Upper Level, Juniper Court<br>Harbourview Plaza<br>Elmwood Ridge, NSW 2199</p>
  </div>
</section>

<section class="card card--back-photo">
  <div class="photo-area" role="img" aria-label="Faded photo of children running outdoors in a garden"></div>
  <div class="photo-veil"></div>
  <h2 class="back__title">Caring about your health</h2>
  <div class="back__rule-h back__rule-h--top"></div>
  <div class="back__rule-v"></div>
  <div class="back__rule-h back__rule-h--bottom"></div>
  <div class="timings">
    <p class="timings__heading">Clinic Timings</p>
    <p class="timings__row"><span class="timings__day">Mon</span><span class="timings__hours">7 am  -  7 pm</span></p>
    <p class="timings__row"><span class="timings__day">Tues</span><span class="timings__hours">7 am  -  12 pm</span></p>
    <p class="timings__row"><span class="timings__day">Wed</span><span class="timings__hours">7 am  -  10 pm</span></p>
    <p class="timings__row"><span class="timings__day">Thurs</span><span class="timings__hours">7 am  -  12 pm</span></p>
    <p class="timings__row"><span class="timings__day">Fri</span><span class="timings__hours">7 am  -  8 pm</span></p>
    <p class="timings__row"><span class="timings__day">Sat</span><span class="timings__hours">8 am  -  10 pm</span></p>
    <p class="timings__row"><span class="timings__day">Sun</span><span class="timings__hours">Off</span></p>
  </div>
  <div class="appointment">
    <p class="appointment__heading">Your Appointment</p>
    <p class="field"><span>Name</span><span class="field__line"></span></p>
    <p class="field field--blank"><span class="field__line"></span></p>
    <p class="field"><span>Date</span><span class="field__line"></span></p>
    <p class="field"><span>time</span><span class="field__line field__line--short"></span><span>am / pm</span></p>
  </div>
  <p class="back__note">24 business hours notice required for cancellations</p>
</section>

<section class="card card--back-tint">
  <h2 class="back__title">Caring about your health</h2>
  <div class="back__rule-h back__rule-h--top"></div>
  <div class="back__rule-v"></div>
  <div class="back__rule-h back__rule-h--bottom"></div>
  <div class="timings">
    <p class="timings__heading">Clinic Timings</p>
    <p class="timings__row"><span class="timings__day">Mon</span><span class="timings__hours">7 am  -  7 pm</span></p>
    <p class="timings__row"><span class="timings__day">Tues</span><span class="timings__hours">7 am  -  12 pm</span></p>
    <p class="timings__row"><span class="timings__day">Wed</span><span class="timings__hours">7 am  -  10 pm</span></p>
    <p class="timings__row"><span class="timings__day">Thurs</span><span class="timings__hours">7 am  -  12 pm</span></p>
    <p class="timings__row"><span class="timings__day">Fri</span><span class="timings__hours">7 am  -  8 pm</span></p>
    <p class="timings__row"><span class="timings__day">Sat</span><span class="timings__hours">8 am  -  10 pm</span></p>
    <p class="timings__row"><span class="timings__day">Sun</span><span class="timings__hours">Off</span></p>
  </div>
  <div class="appointment">
    <p class="appointment__heading">Your Appointment</p>
    <p class="field"><span>Name</span><span class="field__line"></span></p>
    <p class="field field--blank"><span class="field__line"></span></p>
    <p class="field"><span>Date</span><span class="field__line"></span></p>
    <p class="field"><span>time</span><span class="field__line field__line--short"></span><span>am / pm</span></p>
  </div>
  <p class="back__note">24 business hours notice required for cancellations</p>
</section>

</body>
</html>
```